first fantastic look and impression

We are looking for a concept for letterhead, business card, emailfooter and template for invoices or offers for our company in the consultation business.
The dancer is a symbol who we are: it looks simple, but there is a lot of hard work and many years of training in this movement. The look is also what we want: elegant, modern, strong, with a touch of extravaganza
Target Market(s)
Hotelbusiness , Consulting
Font styles to use
Sans Serif
Other font styles liked:
- please give us a option we are open
Requirements
Must have
- We are not typical consultants but sparring partners and coaches for the hotel and that should also be expressed in the design. Maybe there is an icon that supports the whole thing. We are more modern and bolder than our industry colleagues.
we are modern, fresh, agile, fast
Nice to have
- a icon

```html
<!DOCTYPE html>
<html lang="en">
<head>
<meta charset="utf-8">
<title>Norvale business card</title>
<link rel="stylesheet" href="https://fonts.googleapis.com/css2?family=Roboto:wght@300;400&family=Saira+Condensed:wght@600&display=swap">
<style>
  :root {
    --backdrop: #6e6e6e;
    --card-dark: #191919;
    --card-light: #f1f1f1;
    --ink: #111111;
    --emboss-a: #262626;
    --emboss-b: #3a3a3a;
    --art-a: #d9d9d9;
    --art-b: #8a8a8a;
  }
  html, body {
    margin: 0;
    padding: 0;
    width: 1200px;
    height: 1138px;
    overflow: hidden;
    background: var(--backdrop);
  }
  .canvas {
    position: relative;
    width: 1200px;
    height: 1138px;
  }
  .card {
    position: absolute;
    border-radius: 14px;
    box-shadow: 0 4px 10px rgba(0,0,0,0.35);
    overflow: hidden;
  }
  .card--front {
    left: 274px; top: 186px;
    width: 622px; height: 374px;
    background: var(--card-dark);
  }
  .card--back {
    left: 276px; top: 608px;
    width: 618px; height: 374px;
    background: var(--card-light);
    color: var(--ink);
    font-family: "Roboto", sans-serif;
  }
  .dancer-emboss {
    position: absolute;
    left: 162px; top: 60px;
    width: 300px; height: 280px;
    border-radius: 46% 54% 40% 60% / 50% 45% 55% 50%;
    background: radial-gradient(ellipse at 50% 45%, var(--emboss-b), var(--emboss-a) 70%, var(--card-dark));
  }
  .dancer-art {
    position: absolute;
    left: 28px; top: 56px;
    width: 288px; height: 264px;
    border-radius: 46% 54% 40% 60% / 50% 45% 55% 50%;
    background: radial-gradient(ellipse at 50% 45%, var(--art-b), var(--art-a) 75%, var(--card-light));
  }
  .brand {
    position: absolute;
    right: 34px; top: 30px;
    margin: 0;
    font-family: "Roboto", sans-serif;
    font-weight: 300;
    font-size: 56px;
    line-height: 84px;
    letter-spacing: 1px;
    color: var(--ink);
  }
  .identity {
    position: absolute;
    right: 34px; top: 156px;
    text-align: right;
  }
  .identity__name {
    margin: 0;
    font-family: "Saira Condensed", sans-serif;
    font-weight: 600;
    font-size: 27px;
    line-height: 30px;
  }
  .identity__role {
    margin: 2px 0 0;
    font-size: 15.5px;
    line-height: 20px;
  }
  .contact {
    position: absolute;
    right: 34px; top: 240px;
    margin: 0;
    padding: 0;
    list-style: none;
    text-align: right;
    font-size: 15.5px;
  }
  .contact__item {
    display: flex;
    justify-content: flex-end;
    align-items: center;
    gap: 10px;
    height: 24.5px;
  }
  .contact__icon {
    width: 14px; height: 14px;
    fill: var(--ink);
  }
  .contact__address {
    margin-top: 6px;
  }
</style>
</head>
<body>
<div class="canvas">
  <section class="card card--front">
    <div class="dancer-emboss" role="img" aria-label="Embossed line drawing of a leaping dancer holding flowing fabric"></div>
  </section>

  <section class="card card--back">
    <div class="dancer-art" role="img" aria-label="Line drawing of a leaping dancer holding flowing fabric"></div>
    <h1 class="brand">Norvale</h1>
    <div class="identity">
      <p class="identity__name">John Doe Smith</p>
      <p class="identity__role">Managing Director</p>
    </div>
    <ul class="contact">
      <li class="contact__item">828-111-1111
        <svg class="contact__icon" viewBox="0 0 16 16" aria-hidden="true"><path d="M2 5c0-2 2-3 6-3s6 1 6 3v1h-3V5H5v1H2z"/><path d="M4 7h8l2 6H2z"/></svg>
      </li>
      <li class="contact__item">john@yourwebsite.com
        <svg class="contact__icon" viewBox="0 0 16 16" aria-hidden="true"><path d="M1 3h14v10H1z M2 4l6 5 6-5" fill="var(--ink)"/><path d="M2.5 4.5l5.5 4.5 5.5-4.5" fill="none" stroke="#f1f1f1" stroke-width="1.2"/></svg>
      </li>
      <li class="contact__item">www.yourwebsite.com
        <svg class="contact__icon" viewBox="0 0 16 16" aria-hidden="true"><circle cx="8" cy="8" r="7"/><path d="M1 8h14M8 1v14M3 4h10M3 12h10" stroke="#f1f1f1" stroke-width="1" fill="none"/><ellipse cx="8" cy="8" rx="3" ry="7" fill="none" stroke="#f1f1f1" stroke-width="1"/></svg>
      </li>
      <li class="contact__item contact__address">234 Anywhere St., Any City, US 123456</li>
    </ul>
  </section>
</div>
</body>
</html>
```